Global Yoga Apparel Brand Needs a Beautiful Website

We need a website design for a new Yoga brand called Vey. We develop beautiful, stylish, sexy, comfortable yoga leggings, tops, and yoga apparel for women looking to feel their best, look their best and perform their best on and off the yoga mat.
This will go up at http://vey.example/ (which is a landing page right now).
We would like to see simple and clean design where the focus will be on powerful images and clean background space. We will be using Shopify to start building on and here are three sites that we would love to see options based off of the look, layout and feel while making something unique at the same time:
1. Dunt.ca
2. parvasini.com
3. www.k-mole.com
The final design should look clean, beautiful, inspiring, powerful and empowering.
Target Market(s)
mostly Females 21-35 range but will be appealing to women over 35 as well.

```html
<!DOCTYPE html>
<html lang="en">
<head>
<meta charset="utf-8">
<title>Vey — Yoga Apparel</title>
<link href="https://fonts.googleapis.com/css2?family=Oswald:wght@400;500;600&family=Open+Sans:wght@400;600;700&family=Roboto:wght@400;500&display=swap" rel="stylesheet">
<style>
:root{
  --orange:#f5823f;
  --orange-deep:#ee6b2a;
  --price:#e8532a;
  --ink:#333;
  --dark:#141414;
  --darker:#0b0b0b;
  --white:#fff;
  --footer-text:#ddd;
}
*{margin:0;padding:0;box-sizing:border-box}
html,body{width:1200px;height:3056px;overflow:hidden;background:#fff}
body{position:relative;font-family:'Open Sans',sans-serif;color:var(--ink)}
.abs{position:absolute}
ul{list-style:none}

.topbar{left:0;top:0;width:1200px;height:31px;background:var(--orange);color:#fff;font-size:12px}
.topbar .lang{left:98px;top:8px;display:flex;gap:6px;align-items:center;font-size:11px}
.topbar .lang i{width:16px;height:11px;background:#fff;display:inline-block;opacity:.85}
.topbar .phone{left:690px;top:7px;display:flex;gap:8px;align-items:center}
.topbar .mail{left:862px;top:7px;display:flex;gap:8px;align-items:center}
.topbar .socials{left:1006px;top:6px;display:flex;gap:6px}
.topbar .socials span{width:19px;height:19px;border-radius:50%;background:#fff;display:block}

.hero{left:0;top:31px;width:1200px;height:682px;background:linear-gradient(100deg,#2b2a28 0%,#4c4844 45%,#3a3835 70%,#242321 100%)}
.logo{left:98px;top:62px;font-weight:700;font-size:92px;line-height:1;color:#fff;letter-spacing:-2px}
.account-nav{right:98px;top:80px;display:flex;gap:18px;align-items:center;color:#fff;font-size:12.5px}
.cart{width:26px;height:26px;border-radius:50%;border:2px solid #fff;position:relative;display:block}
.cart::after{content:"";position:absolute;right:-5px;top:-6px;width:9px;height:9px;border-radius:50%;background:var(--orange-deep)}
.main-nav{right:98px;top:131px;display:flex;gap:40px;align-items:center;color:#fff;font-size:13.5px;font-weight:600}
.hero-title{left:98px;top:290px;font-family:'Oswald',sans-serif;font-weight:500;font-size:47px;line-height:60px;color:#fff;letter-spacing:.5px;white-space:nowrap}
.hero-lede{left:98px;top:358px;width:360px;font-size:14px;line-height:22px;color:#eee}
.hero-btn{left:98px;top:422px;width:167px;height:40px;border-radius:3px;background:var(--orange);color:#fff;font-size:14px;font-weight:600;text-transform:uppercase;display:flex;align-items:center;justify-content:center}
.dots{left:100px;top:484px;display:flex;gap:8px}
.dots span{width:11px;height:11px;border-radius:50%;background:#fff}

.promo-frame{left:90px;top:648px;width:1020px;height:350px;background:#fff}
.tile{overflow:hidden}
.tile .label{font-family:'Oswald',sans-serif;font-weight:500;font-size:27px;color:#fff}
.tile .price{font-size:19px;color:#fff;margin-top:4px}
.tile .shop{font-size:12.5px;color:#fff;text-decoration:underline;font-style:italic;font-weight:600;margin-top:6px}
.tile-apparel{left:98px;top:656px;width:499px;height:342px;background:linear-gradient(180deg,#8fb1d8 0%,#6f8fb8 55%,#6b6a62 72%,#8a8780 100%)}
.tile-leggings{left:605px;top:656px;width:495px;height:342px;background:linear-gradient(180deg,#8d8a87 0%,#a9a5a1 60%,#7d7a77 100%)}
.tile-apparel .txt{left:45px;top:204px}
.tile-leggings .txt{left:27px;top:48px}

.banner{left:0;top:1051px;width:1200px;height:446px;background:linear-gradient(100deg,#4b5263 0%,#6d7482 45%,#5a606c 75%,#393d46 100%)}
.badge{left:214px;top:1118px;width:318px;height:318px;border-radius:50%;background:var(--orange);border:5px solid #fff;color:#fff;text-align:center;padding-top:74px}
.badge .k1{font-family:'Oswald',sans-serif;font-weight:500;font-size:25px;line-height:1.1}
.badge .k2{font-family:'Oswald',sans-serif;font-weight:500;font-size:36px;line-height:1.15}
.badge p{font-size:12.5px;line-height:18px;margin:6px auto 0;width:250px}
.badge .price{font-size:19px;margin-top:16px}
.badge .shop{font-size:12.5px;text-decoration:underline;font-style:italic;font-weight:600;margin-top:4px}

.section-title{font-family:'Oswald',sans-serif;font-weight:400;font-size:29px;color:#333}
.featured-title{left:0;width:1200px;top:1548px;text-align:center}
.product{width:238px;top:1623px}
.product .shot{width:238px;height:265px;border:1px solid #e4e4e4;background:#f6f6f6;padding:6px}
.product .shot div{width:100%;height:100%}
.product .name{font-family:'Roboto',sans-serif;font-size:14.5px;color:#444;text-align:center;margin-top:14px}
.product .cost{font-family:'Roboto',sans-serif;font-style:italic;font-size:18px;color:var(--price);text-align:center;margin-top:4px}

.collections{left:0;top:2006px;width:1200px;height:491px;background:linear-gradient(180deg,#e4e4e4 0%,#d3d3d3 100%)}
.collections-model{left:80px;top:2040px;width:560px;height:420px;background:radial-gradient(ellipse at 45% 55%,#bcb8b4 0%,#d6d5d4 55%,rgba(214,214,214,0) 75%)}
.collections-title{left:619px;top:2058px;font-weight:500;font-size:32px;color:#2c2c2c}
.col-tile{top:2135px;height:240px}
.col-tops{left:393px;width:352px;background:linear-gradient(135deg,#3b3f47,#7b7d82 50%,#2c2f35)}
.col-apparel{left:752px;width:348px;background:linear-gradient(135deg,#a785c2,#8c6aa8 50%,#5c5d63)}
.col-tile .label{font-family:'Oswald',sans-serif;font-weight:500;font-size:20px;color:#fff;line-height:1.1}
.col-tops .label{left:42px;top:160px}
.col-apparel .label{left:62px;top:36px;text-align:center}

.newsletter{left:0;top:2497px;width:1200px;height:226px;background:linear-gradient(180deg,var(--orange) 0%,#f1773a 100%)}
.newsletter-title{left:0;width:1200px;top:2542px;text-align:center;font-family:'Oswald',sans-serif;font-weight:400;font-size:35px;color:#fff}
.field{top:2617px;height:42px;background:#fff;font-size:12px;color:#666;padding:13px 12px}
.field-name{left:267px;width:250px}
.field-email{left:534px;width:248px}
.subscribe{left:798px;top:2617px;width:135px;height:42px;background:#1c1c1c;color:#fff;font-size:14px;font-weight:600;display:flex;align-items:center;justify-content:center}

.footer{left:0;top:2723px;width:1200px;height:277px;background:var(--dark)}
.foot-head{font-weight:600;font-size:15px;color:#fff;margin-bottom:20px;text-transform:uppercase}
.foot-list li{font-size:12.5px;color:var(--footer-text);line-height:26px}
.brand-col{left:98px;top:2770px;width:300px}
.brand-col .name{font-family:'Oswald',sans-serif;font-weight:500;font-size:33px;color:#fff}
.brand-col p{font-size:11.5px;line-height:20px;color:var(--footer-text);margin-top:14px}
.brand-col .socials{display:flex;gap:12px;margin-top:20px}
.brand-col .socials span{width:26px;height:26px;border-radius:50%;border:1.5px solid #ddd;display:block}
.col-why{left:440px;top:2768px}
.col-account{left:680px;top:2768px}
.col-contact{left:896px;top:2768px;width:230px}
.contact-row{display:flex;gap:14px;color:var(--footer-text);font-size:12.5px;line-height:19px;margin-bottom:16px}
.contact-row svg{flex:none;margin-top:2px}
.contact-row.big{font-size:15px}
.bottombar{left:0;top:3000px;width:1200px;height:56px;background:var(--darker);color:#ccc;font-size:12.5px;text-align:center;line-height:56px}
</style>
</head>
<body>

<div class="abs topbar">
  <div class="abs lang"><i></i>ENGLISH
    <svg width="9" height="6" viewBox="0 0 9 6"><path d="M1 1l3.5 3.5L8 1" stroke="#fff" stroke-width="1.5" fill="none"/></svg></div>
  <div class="abs phone"><svg width="13" height="13" viewBox="0 0 24 24"><path fill="#fff" d="M6.6 10.8a15 15 0 006.6 6.6l2.2-2.2a1 1 0 011-.25 11 11 0 003.6.6 1 1 0 011 1V20a1 1 0 01-1 1A17 17 0 013 4a1 1 0 011-1h3.5a1 1 0 011 1 11 11 0 00.6 3.6 1 1 0 01-.25 1z"/></svg>+901 555 01 23 45</div>
  <div class="abs mail"><svg width="14" height="11" viewBox="0 0 14 11"><rect x="1" y="1" width="12" height="9" fill="none" stroke="#fff" stroke-width="1.3"/><path d="M1 1l6 5 6-5" fill="none" stroke="#fff" stroke-width="1.3"/></svg>info@vey.example</div>
  <div class="abs socials"><span></span><span></span><span></span><span></span></div>
</div>

<header class="abs hero" role="img" aria-label="Photo of a woman holding an inverted yoga pose on a mat against a concrete wall"></header>
<div class="abs logo">vey</div>
<nav class="abs account-nav">
  <span>MY ACCOUNT ▾</span><span>QUICK ORDER ▾</span><span>HELP</span><span class="cart"></span>
</nav>
<nav class="abs main-nav">
  <span>HOME</span><span>ABOUT</span><span>PRODUCTS</span><span>SHOP</span><span>BLOG</span><span>RESOURCES</span>
  <svg width="16" height="16" viewBox="0 0 16 16"><circle cx="6.5" cy="6.5" r="5" stroke="#fff" stroke-width="2" fill="none"/><path d="M10.5 10.5L15 15" stroke="#fff" stroke-width="2"/></svg>
</nav>
<h1 class="abs hero-title">YOGA APPAREL BRAND</h1>
<p class="abs hero-lede">Sed ut perspiciatis unde omnis iste natus error sit voluptatem accusantium doloremque</p>
<a class="abs hero-btn">View Collections</a>
<div class="abs dots"><span></span><span></span><span></span></div>

<div class="abs promo-frame"></div>
<div class="abs tile tile-apparel" role="img" aria-label="Photo of a woman in a handstand split by the lakeside">
  <div class="abs txt"><div class="label">YOGA APPAREL</div><div class="price">$20.00</div><div class="shop">SHOP NOW</div></div>
</div>
<div class="abs tile tile-leggings" role="img" aria-label="Photo of a woman seated in a twist pose in front of a brick wall">
  <div class="abs txt"><div class="label">YOGA LEGGINGS</div><div class="price">$20.00</div><div class="shop">SHOP NOW</div></div>
</div>

<section class="abs banner" role="img" aria-label="Photo of a woman in a three-legged downward dog pose against a grey wall"></section>
<div class="abs badge">
  <div class="k1">COMFORTABLE</div>
  <div class="k2">YOGA LEGGINGS</div>
  <p>Sed ut perspiciatis unde omnis iste natus error sit voluptatem accusantium doloremque</p>
  <div class="price">$20.00</div>
  <div class="shop">SHOP NOW</div>
</div>

<h2 class="abs section-title featured-title">FEATURED PRODUCTS</h2>
<div class="abs product" style="left:98px"><div class="shot"><div role="img" aria-label="Photo of a woman in a warrior lunge" style="background:linear-gradient(180deg,#fafafa,#e9ecf2 60%,#fafafa)"></div></div><div class="name">SED UT PERSPICIATIS UNDE</div><div class="cost">$199.00</div></div>
<div class="abs product" style="left:352px"><div class="shot"><div role="img" aria-label="Photo of a woman in a kneeling backbend" style="background:linear-gradient(180deg,#fafafa,#e6e6e6 60%,#fafafa)"></div></div><div class="name">SED UT PERSPICIATIS UNDE</div><div class="cost">$199.00</div></div>
<div class="abs product" style="left:607px"><div class="shot"><div role="img" aria-label="Photo of a woman in a pigeon pose" style="background:linear-gradient(180deg,#e3f1f6,#cfe6f0 60%,#5aa6d6)"></div></div><div class="name">SED UT PERSPICIATIS UNDE</div><div class="cost">$199.00</div></div>
<div class="abs product" style="left:862px"><div class="shot"><div role="img" aria-label="Photo of a woman seated cross-legged, seen from behind" style="background:linear-gradient(180deg,#fafafa,#ecebf1 55%,#4b3f9e)"></div></div><div class="name">SED UT PERSPICIATIS UNDE</div><div class="cost">$199.00</div></div>

<section class="abs collections"></section>
<div class="abs collections-model" role="img" aria-label="Photo of a woman seated in a low lunge stretching her arms upward"></div>
<h2 class="abs section-title collections-title">NEW COLLECTIONS</h2>
<div class="abs col-tile col-tops" role="img" aria-label="Flat-lay photo of grey yoga tops and a black sports bra"><div class="abs label">YOGA TOPS</div></div>
<div class="abs col-tile col-apparel" role="img" aria-label="Flat-lay photo of lilac yoga apparel, shoes and a rolled mat"><div class="abs label">YOGA<br>APPAREL</div></div>

<section class="abs newsletter"></section>
<h2 class="abs newsletter-title">Join our Newsletter.</h2>
<div class="abs field field-name">Name</div>
<div class="abs field field-email">Email Address</div>
<div class="abs subscribe">SUBSCRIBE</div>

<footer class="abs footer"></footer>
<div class="abs brand-col">
  <div class="name">VEY.YOGA</div>
  <p>Lorem ipsum dolor sit amet conse ctetur adip-isicing elit, sed do eiusmod tempor incididunt ut labore et dolore magna aliqua.</p>
  <div class="socials"><span></span><span></span><span></span><span></span></div>
</div>
<div class="abs col-why"><h4 class="foot-head">Why buy from us</h4><ul class="foot-list">
  <li>Shipping &amp; Returns</li><li>Secure Shopping</li><li>International Shipping</li><li>Affiliates</li><li>Our Blog</li><li>About Our Shop</li></ul></div>
<div class="abs col-account"><h4 class="foot-head">My account</h4><ul class="foot-list">
  <li>My orders</li><li>My credit slips</li><li>My addresses</li><li>My personal info</li><li>Terms and conditions</li><li>Privacy Policy</li></ul></div>
<div class="abs col-contact"><h4 class="foot-head">Contacts</h4>
  <div class="contact-row"><svg width="13" height="17" viewBox="0 0 13 17"><path d="M6.5 0.8a5.7 5.7 0 015.7 5.7c0 4.3-5.7 9.7-5.7 9.7S0.8 10.8 0.8 6.5A5.7 5.7 0 016.5 0.8z" fill="#fff"/><circle cx="6.5" cy="6.3" r="2.2" fill="#141414"/></svg><span>PO BOX 402, 18 Linden Lane, Marrow Vale, NSW 2999</span></div>
  <div class="contact-row big"><svg width="14" height="14" viewBox="0 0 24 24"><path fill="#fff" d="M6.6 10.8a15 15 0 006.6 6.6l2.2-2.2a1 1 0 011-.25 11 11 0 003.6.6 1 1 0 011 1V20a1 1 0 01-1 1A17 17 0 013 4a1 1 0 011-1h3.5a1 1 0 011 1 11 11 0 00.6 3.6 1 1 0 01-.25 1z"/></svg><span>Call Us: 1800 555 019</span></div>
  <div class="contact-row big"><svg width="14" height="11" viewBox="0 0 14 11"><rect x="0.5" y="0.5" width="13" height="10" fill="#fff"/><path d="M0.5 0.5l6.5 5 6.5-5" fill="none" stroke="#141414" stroke-width="1.2"/></svg><span>info@vey.example</span></div>
</div>
<div class="abs bottombar">Copyright © 2016 vey.example. All rights reserved</div>

</body>
</html>
```